Ferncliff Capital - Website Design

We need a website design for a new commercial real estate company called Ferncliff Capital. We're effectively commercial mortgage brokers connecting real estate investors to lenders. We need a website that is simple (not busy), elegant, professional, and user-friendly. A lot of the users will be in their 50's and less tech savvy, so a stream-lined design is best. The website will serve as a portal for lenders to review new financing opportunities, as well as for real estate investors to review terms from lenders.
Updates
Just uploaded our logo.
Target Market(s)
Commercial real estate investors and lenders
Industry/Entity Type
Real Estate
Number of Pages Required
1 page
Colors
Designer to choose colors to be used in the design.
Look and feel

```html
<!DOCTYPE html>
<html lang="en">
<head>
<meta charset="utf-8">
<title>Ferncliff Capital</title>
<link rel="stylesheet" href="https://fonts.googleapis.com/css2?family=Questrial&family=Montserrat:wght@500;600&display=swap">
<style>
:root{
  --navy:#2f3d63;
  --navy-deep:#304069;
  --ink:#3b3f48;
  --muted:#5d6068;
  --white:#ffffff;
  --line:#d7dbe4;
  --footer-text:#dfe3ee;
  --hero-a:#e9e3da;
  --hero-b:#b9aa96;
  --band-a:#58668e;
  --band-b:#7a86a8;
}
*{margin:0;padding:0;box-sizing:border-box}
html,body{width:1200px;height:2347px;overflow:hidden;background:var(--white)}
body{position:relative;font-family:"Questrial",Arial,sans-serif;color:var(--ink)}
.abs{position:absolute}
.center{left:0;width:1200px;text-align:center}

/* header */
.site-header{position:absolute;top:0;left:0;width:1200px;height:111px;background:var(--white);box-shadow:0 2px 6px rgba(0,0,0,.12);z-index:3}
.brand{position:absolute;left:99px;top:38px;font-family:"Montserrat",sans-serif;font-weight:600;font-size:30px;letter-spacing:1px;color:var(--navy)}
.nav{position:absolute;top:53px;left:0;font-size:14px;color:var(--navy);letter-spacing:.3px}
.nav a{position:absolute;white-space:nowrap;color:inherit;text-decoration:none}
.nav .active{border-bottom:2px solid var(--navy);padding-bottom:8px}

/* hero */
.hero{position:absolute;top:111px;left:0;width:1200px;height:648px}
.hero-photo{position:absolute;inset:0;background:linear-gradient(100deg,var(--hero-b) 0%,var(--hero-a) 35%,#f2efea 55%,#cfc5b8 80%,#8f8577 100%)}
.hero-shade{position:absolute;inset:0;background:rgba(60,60,70,.28)}
.hero-title{top:225px;font-family:"Montserrat",sans-serif;font-weight:600;font-size:74px;letter-spacing:2px;color:var(--white)}
.hero-sub{top:313px;font-size:20px;color:var(--white)}
.hero-arrow{position:absolute;top:280px}
.hero-curve{position:absolute;left:0;bottom:0}

/* intro */
.intro-title{top:790px;font-size:37px;color:var(--navy);letter-spacing:.5px}
.intro-text{position:absolute;left:120px;width:960px;text-align:center;font-size:13.5px;line-height:26.5px;color:var(--muted)}

/* about band */
.about-band{position:absolute;top:1103px;left:0;width:1200px;height:375px;background:linear-gradient(90deg,var(--band-a),var(--band-b) 55%,var(--band-a))}
.about-title{top:55px;font-size:58px;color:var(--white)}
.about-text{position:absolute;left:150px;top:142px;width:900px;text-align:center;font-size:15px;line-height:23px;color:var(--white)}
.outline-btn{position:absolute;left:493px;top:249px;width:213px;height:50px;border:2px solid var(--white);color:var(--white);font-family:"Montserrat",sans-serif;font-weight:500;font-size:18px;text-align:center;line-height:46px;letter-spacing:.5px}

/* services */
.services-title{top:1545px;font-size:34px;color:var(--ink)}
.service{position:absolute;top:1640px;width:270px;text-align:center}
.service-icon{display:block;margin:0 auto}
.service-name{margin-top:16px;font-size:17px;color:var(--ink);letter-spacing:.3px}
.service-text{margin:10px auto 0;width:210px;font-size:11.5px;line-height:19.5px;color:var(--muted)}
.read-more{display:inline-block;margin-top:14px;width:130px;height:38px;border:1.5px solid var(--navy);color:var(--navy);font-size:14px;line-height:35px}

/* footer */
.site-footer{position:absolute;top:2004px;left:0;width:1200px;height:343px;background:var(--navy-deep);color:var(--footer-text)}
.footer-heading{position:absolute;top:46px;font-size:18px;color:var(--white);letter-spacing:.3px}
.footer-link{position:absolute;font-size:14.5px;color:var(--footer-text)}
.footer-divider{position:absolute;top:48px;width:1px;height:200px;background:rgba(255,255,255,.12)}
.contact-line{position:absolute;left:487px;font-size:14.5px;line-height:26px;color:var(--footer-text)}
.email-field{position:absolute;left:776px;top:114px;width:219px;height:38px;background:var(--white);color:#b7bbc5;font-size:13px;line-height:38px;padding-left:14px;letter-spacing:.5px}
.subscribe-btn{position:absolute;left:995px;top:114px;width:106px;height:38px;background:#26345a;color:var(--white);font-size:14px;line-height:38px;text-align:center}
.social{position:absolute;top:167px;width:38px;height:38px;border-radius:50%;background:var(--white)}
.footer-rule{position:absolute;left:99px;top:271px;width:1002px;height:1px;background:rgba(255,255,255,.45)}
.copyright{position:absolute;left:99px;top:295px;font-size:13.5px;color:var(--footer-text)}
</style>
</head>
<body>

<header class="site-header">
  <div class="brand">FERNCLIFF CAPITAL</div>
  <nav class="nav">
    <a class="active" style="left:524px">HOME</a>
    <a style="left:604px">ABOUT US</a>
    <a style="left:702px">OUR SERVICES</a>
    <a style="left:834px">MORTGAGE BROKERS</a>
    <a style="left:1015px">CONTACT US</a>
  </nav>
</header>

<section class="hero">
  <div class="hero-photo" role="img" aria-label="Photo of a businessman in a white shirt and tie reviewing documents at an office desk"></div>
  <div class="hero-shade"></div>
  <h1 class="abs center hero-title">FERNCLIFF CAPITAL</h1>
  <p class="abs center hero-sub">We're effectively commercial mortgage brokers connecting real estate investors to lenders.</p>
  <svg class="hero-arrow" style="left:32px" width="16" height="34" viewBox="0 0 16 34"><path d="M14 2 L3 17 L14 32" fill="none" stroke="#fff" stroke-width="1.6" opacity=".8"/></svg>
  <svg class="hero-arrow" style="left:1144px" width="16" height="34" viewBox="0 0 16 34"><path d="M2 2 L13 17 L2 32" fill="none" stroke="#fff" stroke-width="1.6" opacity=".8"/></svg>
  <svg class="hero-curve" width="1200" height="70" viewBox="0 0 1200 70"><path d="M0 70 Q600 -60 1200 70 Z" fill="#fff"/></svg>
</section>

<h2 class="abs center intro-title">We are a new Commercial Real Estate Company</h2>
<p class="intro-text" style="top:847px">Lorem ipsum dolor sit amet, consectetur adipiscing elit, sed do eiusmod tempor incididunt ut labore et dolore magna aliqua. Ut enim ad minim veniam, quis nostrud exercitation ullamco laboris nisi ut aliquip ex ea commodo consequat. Duis aute irure dolor in reprehenderit in voluptate velit esse cillum dolore eu fugiat nulla pariatur.</p>
<p class="intro-text" style="top:949px">Neque porro quisquam est, qui dolorem ipsum quia dolor sit amet, consectetur, adipisci velit, sed quia non numquam eius modi tempora incidunt ut labore et dolore magnam aliquam quaerat voluptatem. Ut enim ad minima veniam.</p>

<section class="about-band" role="img" aria-label="Soft blue-tinted photo of business people meeting at a table">
  <h2 class="abs center about-title">About Ferncliff Capital</h2>
  <p class="about-text">At vero eos et accusamus et iusto odio dignissimos ducimus qui blanditiis praesentium voluptatum deleniti atque corrupti quos dolores et quas molestias excepturi sint occaecati cupiditate non provident, similique sunt in culpa qui officia deserunt mollitia animi, id est laborum et dolorum fuga. Et harum quidem rerum facilis est et expedita distinctio.</p>
  <div class="outline-btn">LEARN MORE</div>
</section>

<h2 class="abs center services-title">Our Services</h2>

<div class="service" style="left:68px">
  <svg class="service-icon" width="124" height="124" viewBox="0 0 124 124"><circle cx="62" cy="62" r="60" fill="none" stroke="#2f3d63" stroke-width="2"/><circle cx="62" cy="62" r="56" fill="#2f3d63"/><rect x="44" y="46" width="30" height="30" rx="4" fill="none" stroke="#fff" stroke-width="3"/><path d="M56 66 L78 44 L83 49 L61 71 L54 73 Z" fill="#fff"/></svg>
  <div class="service-name">FREE REGISTRATION</div>
  <p class="service-text">Sed ut perspiciatis unde omnis iste natus error sit voluptatem accusantium doloremque laudantium.</p>
  <span class="read-more">READ MORE</span>
</div>

<div class="service" style="left:333px">
  <svg class="service-icon" width="124" height="124" viewBox="0 0 124 124"><circle cx="62" cy="62" r="60" fill="none" stroke="#2f3d63" stroke-width="2"/><circle cx="62" cy="62" r="56" fill="#2f3d63"/><rect x="46" y="43" width="30" height="38" rx="3" fill="none" stroke="#fff" stroke-width="2.5"/><rect x="54" y="39" width="14" height="8" rx="2" fill="#fff"/><path d="M52 55 H70 M52 62 H66 M52 69 H62" stroke="#fff" stroke-width="2"/><circle cx="74" cy="76" r="7" fill="#fff"/><path d="M71 76 L73.5 78.5 L77.5 73.5" fill="none" stroke="#2f3d63" stroke-width="2"/></svg>
  <div class="service-name">PROPERTY APPRAISAL</div>
  <p class="service-text">Sed ut perspiciatis unde omnis iste natus error sit voluptatem accusantium doloremque laudantium.</p>
  <span class="read-more">READ MORE</span>
</div>

<div class="service" style="left:596px">
  <svg class="service-icon" width="124" height="124" viewBox="0 0 124 124"><circle cx="62" cy="62" r="60" fill="none" stroke="#2f3d63" stroke-width="2"/><circle cx="62" cy="62" r="56" fill="#2f3d63"/><path d="M62 84 C52 70 48 63 48 56 A14 14 0 0 1 76 56 C76 63 72 70 62 84 Z" fill="#fff"/><circle cx="62" cy="56" r="5" fill="#2f3d63"/></svg>
  <div class="service-name">LARGE COVERAGE</div>
  <p class="service-text">Sed ut perspiciatis unde omnis iste natus error sit voluptatem accusantium doloremque laudantium.</p>
  <span class="read-more">READ MORE</span>
</div>

<div class="service" style="left:860px">
  <svg class="service-icon" width="124" height="124" viewBox="0 0 124 124"><circle cx="62" cy="62" r="60" fill="none" stroke="#2f3d63" stroke-width="2"/><circle cx="62" cy="62" r="56" fill="#2f3d63"/><path d="M40 62 L62 42 L84 62" fill="none" stroke="#fff" stroke-width="3"/><path d="M46 57 V82 H78 V57" fill="none" stroke="#fff" stroke-width="2.5"/><rect x="56" y="66" width="12" height="16" fill="none" stroke="#fff" stroke-width="2.5"/><rect x="50" y="62" width="6" height="6" fill="#fff"/></svg>
  <div class="service-name">SELECTING A HOUSE</div>
  <p class="service-text">Sed ut perspiciatis unde omnis iste natus error sit voluptatem accusantium doloremque laudantium.</p>
  <span class="read-more">READ MORE</span>
</div>

<footer class="site-footer">
  <div class="footer-heading" style="left:99px">QUICK LINKS</div>
  <div class="footer-link" style="left:99px;top:86px">Home</div>
  <div class="footer-link" style="left:99px;top:117px">About Us</div>
  <div class="footer-link" style="left:99px;top:149px">Our Services</div>
  <div class="footer-link" style="left:99px;top:180px">Mortgage Brokers</div>
  <div class="footer-link" style="left:280px;top:86px">Terms of Service</div>
  <div class="footer-link" style="left:280px;top:117px">Privacy Policy</div>
  <div class="footer-link" style="left:280px;top:149px">Contact Us</div>
  <div class="footer-divider" style="left:426px"></div>

  <div class="footer-heading" style="left:487px">CONTACT INFO</div>
  <div class="contact-line" style="top:80px">Ferncliff Capital , City<br>Name , Country Code.</div>
  <svg class="abs" style="left:487px;top:149px" width="14" height="14" viewBox="0 0 14 14"><rect width="14" height="14" rx="3" fill="#dfe3ee"/><path d="M4 3 L6 3 L7 5.5 L5.8 6.5 C6.3 7.6 6.9 8.3 7.8 8.8 L8.8 7.6 L11 8.6 L11 10.6 C7 11 3.5 7.5 4 3 Z" fill="#304069"/></svg>
  <div class="contact-line" style="left:512px;top:142px">+00 123 45 67 890</div>
  <svg class="abs" style="left:487px;top:182px" width="14" height="11" viewBox="0 0 14 11"><rect width="14" height="11" rx="1" fill="#dfe3ee"/><path d="M0.5 1 L7 6 L13.5 1" fill="none" stroke="#304069" stroke-width="1.3"/></svg>
  <div class="contact-line" style="left:512px;top:174px">info@domainname.com</div>
  <div class="footer-divider" style="left:727px"></div>

  <div class="footer-heading" style="left:774px">SIGN UP FOR NEWSLETTERS</div>
  <div class="footer-link" style="left:774px;top:83px">Please sign up here for latest news</div>
  <div class="email-field">EMAIL ADDRESS</div>
  <div class="subscribe-btn">SUBSCRIBE</div>
  <div class="social" style="left:776px" role="img" aria-label="Social network link"></div>
  <div class="social" style="left:824px" role="img" aria-label="Social network link"></div>
  <div class="social" style="left:874px" role="img" aria-label="Social network link"></div>
  <div class="social" style="left:921px" role="img" aria-label="Social network link"></div>

  <div class="footer-rule"></div>
  <div class="copyright">© 2017 FERNCLIFF CAPITAL.&nbsp; All right reserved . Term of Use</div>
</footer>

</body>
</html>
```